RESINE DENTAIRE ROSE box for dental resine pink to repair dentures broken

I will need a design for a box of pink dental resin. It is a pink dental resin which is intended for sale to individuals on Brindleway to repair or make small touch-ups or modifications to their dental prostheses. The title RESINE DENTAIRE ROSE must be clearly visible as well as the company logo. .I leave it to your creative mind to make an attractive and highly impactful and clearly visible sales design.
It is also necessary to make it clear to buyers through text or a vector image the purpose of the product: to repair a dental prosthesis.
Faible participation designers
Particulars who have need to repair their dentures

```html
<!DOCTYPE html>
<html lang="fr">
<head>
<meta charset="utf-8">
<title>Résine Dentaire Rose – Box design</title>
<link href="https://fonts.googleapis.com/css2?family=Montserrat:wght@400;500;600;700&display=swap" rel="stylesheet">
<style>
  :root{
    --green:#8cc63f;
    --green-dark:#6fae2c;
    --title-green:#3cb54a;
    --silver-light:#f4f4f4;
    --silver-mid:#d5d6d8;
    --silver-dark:#a9abae;
    --grey-text:#5f6062;
    --white:#ffffff;
    --page:#ffffff;
  }
  html,body{margin:0;padding:0;overflow:hidden;background:var(--page);}
  .canvas{position:relative;width:1200px;height:3591px;overflow:hidden;background:var(--page);font-family:'Montserrat',sans-serif;}
  .front-panel{position:absolute;left:207px;top:78px;width:786px;height:950px;}
  .dieline{position:absolute;left:180px;top:2860px;width:840px;height:680px;}
  .title{font-family:'Montserrat',sans-serif;font-weight:600;fill:var(--title-green);}
  .subtitle{font-family:'Montserrat',sans-serif;font-weight:500;fill:var(--grey-text);}
  .badge-label{font-family:'Montserrat',sans-serif;font-weight:700;fill:var(--white);}
  .brand{font-family:'Montserrat',sans-serif;font-weight:600;fill:var(--white);}
  .fine{font-family:'Montserrat',sans-serif;font-weight:400;fill:var(--white);}
</style>
</head>
<body>
<div class="canvas">

<svg width="0" height="0" style="position:absolute" aria-hidden="true">
  <defs>
    <linearGradient id="silver" x1="0" y1="0" x2="1" y2="0">
      <stop offset="0" stop-color="#c9cacc"/>
      <stop offset="0.45" stop-color="#f5f5f5"/>
      <stop offset="1" stop-color="#cfd0d2"/>
    </linearGradient>
    <linearGradient id="rim" x1="0" y1="0" x2="1" y2="1">
      <stop offset="0" stop-color="#eeeeee"/>
      <stop offset="0.5" stop-color="#9d9fa2"/>
      <stop offset="1" stop-color="#e8e8e8"/>
    </linearGradient>
    <linearGradient id="badgeShield" x1="0" y1="0" x2="0" y2="1">
      <stop offset="0" stop-color="#a6d65a"/>
      <stop offset="1" stop-color="#5daa2c"/>
    </linearGradient>
    <radialGradient id="teethArt" cx="0.5" cy="0.5" r="0.6">
      <stop offset="0" stop-color="#ffffff"/>
      <stop offset="0.6" stop-color="#f4a6cf"/>
      <stop offset="1" stop-color="#e573b0"/>
    </radialGradient>
    <radialGradient id="iconArt" cx="0.5" cy="0.5" r="0.6">
      <stop offset="0" stop-color="#b7e07a"/>
      <stop offset="1" stop-color="#7cbf37"/>
    </radialGradient>

    <symbol id="face" viewBox="0 0 786 950">
      <rect class="face-bg" width="786" height="950" fill="var(--green)"/>
      <path class="shield-rim" d="M0 0H786V215C786 470 690 640 393 802C96 640 0 470 0 215Z" fill="url(#rim)"/>
      <path class="shield-plate" d="M0 0H786V190C770 440 670 610 393 770C116 610 16 440 0 190Z" fill="url(#silver)"/>

      <text class="title" x="393" y="237" text-anchor="middle" font-size="63">RESINE DENTAIRE</text>
      <text class="title" x="393" y="323" text-anchor="middle" font-size="63">ROSE</text>
      <text class="subtitle" x="393" y="433" text-anchor="middle" font-size="38">REPAIR</text>
      <text class="subtitle" x="393" y="482" text-anchor="middle" font-size="38">DENTAL PROSTHESIS</text>

      <g class="check-shield">
        <path d="M393 590L455 614V660C455 710 425 735 393 752C361 735 331 710 331 660V614Z" fill="url(#badgeShield)" stroke="#d9efc0" stroke-width="4"/>
        <path d="M366 664L388 686L424 648" fill="none" stroke="#ffffff" stroke-width="12" stroke-linecap="round" stroke-linejoin="round"/>
      </g>

      <g class="feature ease">
        <circle cx="115" cy="612" r="46" fill="var(--white)"/>
        <circle cx="115" cy="612" r="40" fill="url(#iconArt)" role="img" aria-label="Icône main, facilité d'emploi"/>
        <text class="badge-label" x="112" y="680" text-anchor="middle" font-size="15">FACILITÉ D'EMPLOI</text>
      </g>
      <g class="feature small-repairs">
        <circle cx="230" cy="747" r="64" fill="var(--white)"/>
        <circle cx="230" cy="747" r="55" fill="url(#teethArt)" role="img" aria-label="Illustration de prothèse dentaire réparée"/>
        <text class="badge-label" x="230" y="838" text-anchor="middle" font-size="15">PETITES RÉPARATIONS</text>
      </g>
      <g class="feature loose-tooth">
        <circle cx="558" cy="747" r="64" fill="var(--white)"/>
        <circle cx="558" cy="747" r="55" fill="url(#teethArt)" role="img" aria-label="Illustration de prothèse avec dent détachée"/>
        <text class="badge-label" x="558" y="838" text-anchor="middle" font-size="15">DENT DÉTACHÉE</text>
      </g>
      <g class="feature ten-minutes">
        <circle cx="673" cy="610" r="46" fill="var(--white)"/>
        <circle cx="673" cy="610" r="40" fill="url(#iconArt)" role="img" aria-label="Icône chronomètre, en 10 minutes"/>
        <text class="badge-label" x="673" y="680" text-anchor="middle" font-size="15">EN 10 MINUTES</text>
      </g>
    </symbol>
  </defs>
</svg>

<svg class="front-panel" viewBox="0 0 786 950" role="group" aria-label="Face avant de la boîte">
  <use href="#face" width="786" height="950"/>
</svg>

<svg class="dieline" viewBox="0 0 840 680" role="group" aria-label="Patron déplié de la boîte">
  <!-- top flap with brand -->
  <path d="M63 165V40Q63 12 91 12H305Q333 12 333 40V165Z" fill="var(--green)"/>
  <rect x="118" y="87" width="26" height="26" fill="var(--white)"/>
  <text class="brand" x="154" y="98" font-size="14">LABORATOIRE</text>
  <text class="brand" x="154" y="114" font-size="14">VERADENT</text>

  <!-- left glue flap -->
  <path d="M63 177L10 187V478L63 490Z" fill="var(--green)"/>

  <!-- front -->
  <use href="#face" x="63" y="165" width="270" height="326"/>

  <!-- side panel 1 -->
  <path d="M333 165V110L355 100L383 60H420L445 100V165Z" fill="var(--green)"/>
  <rect x="333" y="165" width="112" height="326" fill="var(--green)"/>
  <path d="M333 491H445V540L420 580H358L333 540Z" fill="var(--green)"/>
  <g transform="translate(360 175) rotate(90)">
    <text class="fine" x="0" y="0" font-size="7">Résine acrylique rose pour prothèse dentaire</text>
    <text class="fine" x="0" y="-14" font-size="7">Mélanger poudre et liquide, appliquer, laisser durcir</text>
    <text class="fine" x="0" y="-28" font-size="7">Usage externe, tenir hors de portée des enfants</text>
  </g>
  <rect x="392" y="420" width="14" height="14" fill="var(--white)"/>
  <g transform="translate(420 392) rotate(90)">
    <text class="brand" x="0" y="0" font-size="9">LABORATOIRE VERADENT</text>
  </g>

  <!-- back / second face -->
  <use href="#face" x="445" y="165" width="270" height="326"/>
  <path d="M445 491H715V640Q715 668 687 668H473Q445 668 445 640Z" fill="var(--green)"/>
  <g transform="translate(580 600) rotate(180)">
    <rect x="-100" y="-16" width="26" height="26" fill="var(--white)"/>
    <text class="brand" x="-64" y="-5" font-size="14">LABORATOIRE</text>
    <text class="brand" x="-64" y="11" font-size="14">VERADENT</text>
  </g>

  <!-- side panel 2 -->
  <path d="M715 165V100L740 60H775L800 100L828 110V165Z" fill="var(--green)"/>
  <rect x="715" y="165" width="113" height="326" fill="var(--green)"/>
  <path d="M715 491H828V540L803 580H740L715 540Z" fill="var(--green)"/>
  <g transform="translate(752 470) rotate(-90)">
    <text class="fine" x="0" y="0" font-size="7">Poudre: polyméthacrylate de méthyle</text>
    <text class="fine" x="0" y="12" font-size="7">Liquide: méthacrylate de méthyle</text>
  </g>
  <rect x="760" y="215" width="14" height="14" fill="var(--white)"/>
  <g transform="translate(760 300) rotate(-90)">
    <text class="brand" x="0" y="0" font-size="9">LABORATOIRE VERADENT</text>
  </g>
</svg>

</div>
</body>
</html>
```